Web Design Project

We are an IT System Integrator. We provide Korvin 450 ERP System, CRM etc. We also provide hardware, networking servicing. Please look at www.zolvantix.com.sg. They provide the same service as us. We like to redesign our web site. I will attached the color that I prefer for reference.

Our website is www.tadurk.com.sg.  It has been created about 14 years ago.  We are trying to revamp it with a new look and information.   The new website must be informative, fast.    I have attached an attachment which show the color that I prefer(brownish golden).   

Our competitor (www.zolvantix.com) is carrying the same trade as us.  They have all the informations In their website that we will like to have.  Therefore I recommend you to take a look at my competitor website and have a better   
understanding on the kind of information I would like to have for my new website.

This project is guarantee to the person with the best design.  We can have it guarantee.

Target Market(s)

Corporate and companies

Industry/Entity Type

Hardware

```html
<!DOCTYPE html>
<html lang="en">
<head>
<meta charset="utf-8">
<title>Tadurk – IT System Integrator</title>
<link rel="stylesheet" href="https://fonts.googleapis.com/css2?family=Signika:wght@400;600;700&family=Roboto:wght@400;500;700&display=swap">
<style>
:root{
  --gold-light:#f1e3b4;
  --gold:#c9a85c;
  --gold-dark:#8d6a22;
  --brown:#8a6422;
  --brown-deep:#4a3208;
  --brown-mid:#6e4e14;
  --cream:#f3ecd9;
  --card-bg:#efefef;
  --ink:#222;
  --white:#fff;
}
*{box-sizing:border-box;margin:0;padding:0}
html,body{width:1200px;height:1011px;overflow:hidden}
body{position:relative;font-family:"Roboto",Arial,sans-serif;color:var(--ink);background:var(--cream)}
.abs{position:absolute}

/* header */
.site-header{left:0;top:0;width:1200px;height:101px;background:linear-gradient(180deg,var(--gold-light) 0%,#e3cd8a 45%,var(--gold) 80%,#b08a3c 100%)}
.header-band{left:0;top:101px;width:1200px;height:12px;background:linear-gradient(180deg,#a9a9a9,#7c7c7c)}
.brand{left:288px;top:30px;display:flex;align-items:center;gap:10px;font-family:"Signika",sans-serif;font-weight:700;font-size:34px;color:var(--gold-dark)}
.brand-dot{width:22px;height:22px;border-radius:50%;background:var(--gold-dark)}
.util-links{left:644px;top:22px;display:flex;gap:10px;font-size:9px;color:#333}
.search{left:793px;top:19px;width:108px;height:19px;border-radius:10px;background:var(--white);font-size:9px;color:#555;padding:4px 10px}
.search-icon{left:905px;top:19px}
.main-nav{left:485px;top:73px;display:flex;font-family:"Signika",sans-serif;font-weight:600;font-size:11.5px;color:var(--white);letter-spacing:.2px;white-space:nowrap}

/* hero */
.hero{left:0;top:113px;width:1200px;height:465px;overflow:hidden}
.hero-photo{left:0;top:0;width:1200px;height:465px;background:linear-gradient(90deg,#2e2a28 0%,#55463a 25%,#b89b7c 45%,#c9ad8a 70%,#b39170 100%)}
.hero-overlay{left:0;top:0}
.hero-title{left:602px;top:60px;font-family:"Signika",sans-serif;font-weight:600;font-size:29px;color:var(--white);text-shadow:0 1px 2px rgba(0,0,0,.4)}
.hero-sub{left:602px;top:96px;font-family:"Signika",sans-serif;font-size:13.5px;color:var(--white)}
.thumbs{left:781px;top:192px;display:flex;gap:5px}
.thumb{width:33px;height:33px;border:2px solid var(--white);background:linear-gradient(135deg,#c9a99a,#7a8aa0)}

.quote-bar{left:268px;top:235px;width:664px;height:31px;background:var(--brown);display:flex;align-items:center;padding-left:12px}
.quote-title{font-family:"Signika",sans-serif;font-weight:600;font-size:17px;color:var(--white);width:157px;white-space:nowrap}
.quote-field{width:142px;height:18px;border-radius:9px;background:var(--white);font-size:9.5px;color:#999;padding:3px 10px;margin-right:12px}
.quote-go{left:898px;top:238px}

.feature{top:276px;width:156px;height:110px;background:var(--card-bg);padding:8px 7px}
.feature-mark{height:44px;display:flex;align-items:center}
.wordmark{font-family:"Signika",sans-serif;font-weight:600;font-size:26px;color:var(--brown)}
.feature-arrow{position:absolute;right:8px;top:8px}
.feature h3{font-family:"Signika",sans-serif;font-weight:600;font-size:11px;color:var(--brown);margin-top:6px}
.feature p{font-size:7.5px;line-height:9px;color:#333;margin-top:3px}

.partners{left:268px;top:399px;width:665px;height:50px;background:#e9e9e9;display:flex;align-items:center;padding-left:7px}
.partners-label{font-family:"Signika",sans-serif;font-weight:600;font-size:12.5px;color:var(--brown-mid);width:88px}
.partner-badge{background:#555;margin-right:32px}
.partner-wide{width:62px;height:22px;border-radius:4px}
.partner-round{width:34px;height:34px;border-radius:50%}

/* content */
.panel{background:var(--white);border:1px solid #c9b58a;box-shadow:0 4px 6px rgba(0,0,0,.15)}
.panel-head{height:31px;background:linear-gradient(180deg,#b89447,var(--brown));font-family:"Signika",sans-serif;font-size:14.5px;color:var(--white);padding:7px 20px}
.about{left:269px;top:592px;width:437px;height:193px}
.about-photo{position:absolute;left:14px;top:49px;width:148px;height:126px;background:linear-gradient(180deg,#3a3a3a,#1c1c1c);border:5px solid #eee}
.about-hello{position:absolute;left:178px;top:50px;font-size:21px;font-weight:400}
.about-text{position:absolute;left:178px;top:86px;width:246px;font-size:8.2px;line-height:10.3px;color:#333}
.readmore{position:absolute;left:174px;top:166px;width:60px;height:16px;background:var(--brown);color:var(--white);font-size:8.5px;text-align:center;line-height:16px}

.news{left:721px;top:592px;width:212px;height:193px}
.news-dots{position:absolute;right:8px;top:12px;display:flex;gap:4px}
.news-dots i{width:6px;height:6px;border-radius:50%;background:#eee;display:block}
.news-dots i.on{background:#5aa0b0}
.news-date{position:absolute;left:9px;top:42px;width:32px;height:62px;text-align:center;font-size:8px;font-weight:700;line-height:10px}
.news-day{display:block;width:32px;height:28px;border:2px solid var(--brown);font-size:17px;line-height:24px;margin-bottom:4px;background:var(--white)}
.news-photo{position:absolute;left:47px;top:43px;width:161px;height:63px;background:linear-gradient(135deg,#e8e8e8,#6c6c6c 60%,#dadada)}
.news-title{position:absolute;left:9px;top:121px;font-size:11px;font-weight:500}
.news-text{position:absolute;left:9px;top:140px;width:195px;font-size:7.5px;line-height:9.5px;color:#333}

/* footer */
.footer-band{left:0;top:804px;width:1200px;height:10px;background:linear-gradient(180deg,#8a8a8a,#5c5c5c)}
.site-footer{left:0;top:814px;width:1200px;height:197px;background:radial-gradient(ellipse at 50% 40%,#7a5a20 0%,var(--brown-deep) 70%);color:var(--white)}
.newsletter{left:273px;top:10px;width:147px;height:23px;background:#9c9c9c;padding:3px}
.newsletter div{background:var(--white);height:17px;font-size:7.5px;color:#666;padding:3px 8px}
.newsletter-go{left:403px;top:15px}
.socials{left:274px;top:40px;display:flex;gap:1px}
.socials span{width:24px;height:24px;background:#8a8a8a}
.socials span:first-child{background:#3b5a9a}
.company{left:276px;top:75px;font-size:7.5px;line-height:12.8px;font-style:normal}
.company strong{font-size:10.5px;display:block;margin-bottom:2px}
.foot-col{top:10px;font-size:7.5px;line-height:12.6px;letter-spacing:.4px;color:#f2e6c9}
.foot-col h4{font-family:"Signika",sans-serif;font-weight:600;font-size:8px;letter-spacing:1px;color:var(--white);margin-bottom:6px}
.foot-rule{left:0;top:168px;width:1200px;height:1px;background:rgba(255,255,255,.35)}
.copyright{left:276px;top:182px;font-size:6.5px}
.legal{left:811px;top:182px;font-size:6.5px}
</style>
</head>
<body>

<header class="abs site-header">
  <div class="abs brand"><span>tadurk</span><span class="brand-dot"></span></div>
  <nav class="abs util-links"><span>· FAQ</span><span>· Resources</span><span>· Log Incident</span></nav>
  <div class="abs search">Search</div>
  <svg class="abs search-icon" width="16" height="16" viewBox="0 0 16 16"><circle cx="9" cy="6.5" r="5" fill="none" stroke="#fff" stroke-width="1.6"/><line x1="5.5" y1="10" x2="1.5" y2="14.5" stroke="#fff" stroke-width="2"/></svg>
  <nav class="abs main-nav">
    <span style="width:78px">SOLUTIONS</span><span style="width:78px">HARDWARE</span><span style="width:79px">SERVICES</span><span style="width:70px">CLIENTS</span><span style="width:76px">ABOUT US</span><span>CONTACT US</span>
  </nav>
</header>
<div class="abs header-band"></div>

<section class="abs hero">
  <div class="abs hero-photo" role="img" aria-label="Photo of a warehouse worker in a cap handling boxes"></div>
  <svg class="abs hero-overlay" width="1200" height="465" viewBox="0 0 1200 465">
    <polygon points="592,40 1200,0 1200,465 1045,465 595,170 528,92" fill="#8a6422" opacity=".72"/>
    <polygon points="528,92 592,40 592,125" fill="#5e4216" opacity=".6"/>
  </svg>
  <h1 class="abs hero-title">Warehouse Management</h1>
  <p class="abs hero-sub">Achieve warehouse visibility and maximize its storage</p>
  <div class="abs thumbs" role="img" aria-label="Slide preview thumbnails">
    <span class="thumb"></span><span class="thumb" style="background:linear-gradient(135deg,#8ab8d0,#3c6e8e)"></span><span class="thumb" style="background:linear-gradient(135deg,#6a7a9a,#1c2230)"></span><span class="thumb" style="background:linear-gradient(135deg,#b08a70,#5a3a2a)"></span>
  </div>

  <form class="abs quote-bar">
    <span class="quote-title">GET FREE QUOTE</span>
    <span class="quote-field">name</span><span class="quote-field">email</span><span class="quote-field">mobile</span>
  </form>
  <svg class="abs quote-go" width="25" height="25" viewBox="0 0 25 25"><circle cx="12.5" cy="12.5" r="12" fill="#f6f0e0"/><path d="M10 7l6 5.5-6 5.5" fill="none" stroke="#6e4e14" stroke-width="2.6"/></svg>

  <article class="abs feature" style="left:269px">
    <div class="feature-mark"><span class="wordmark">Korvin</span></div>
    <svg class="feature-arrow" width="8" height="14"><path d="M1 1l6 6-6 6" fill="none" stroke="#6e4e14" stroke-width="2"/></svg>
    <h3>KORVIN Certified</h3>
    <p>Lorem ipsum dolor sit amet, consectetur adipiscing elit. Integer id dolor magna. Aliquam elit metus, laoreet et mattis eu,</p>
  </article>
  <article class="abs feature" style="left:439px">
    <div class="feature-mark"><svg width="76" height="40" viewBox="0 0 76 40"><rect x="2" y="3" width="28" height="20" rx="3" fill="none" stroke="#222" stroke-width="2"/><path d="M8 23v7l6-7" fill="none" stroke="#222" stroke-width="2"/><rect x="32" y="9" width="40" height="26" rx="4" fill="none" stroke="#222" stroke-width="2"/><path d="M64 35v5l-6-5" fill="none" stroke="#222" stroke-width="2"/><circle cx="44" cy="22" r="2.4" fill="#8d6a22"/><circle cx="52" cy="22" r="2.4" fill="#8d6a22"/><circle cx="60" cy="22" r="2.4" fill="#8d6a22"/><rect x="8" y="11" width="4" height="3" fill="#222"/><rect x="14" y="11" width="4" height="3" fill="#222"/><rect x="20" y="11" width="4" height="3" fill="#222"/></svg></div>
    <svg class="feature-arrow" width="8" height="14"><path d="M1 1l6 6-6 6" fill="none" stroke="#6e4e14" stroke-width="2"/></svg>
    <h3>Success Stories</h3>
    <p>Lorem ipsum dolor sit amet, consectetur adipiscing elit. Integer id dolor magna. Aliquam elit metus, laoreet et mattis eu,</p>
  </article>
  <article class="abs feature" style="left:609px">
    <div class="feature-mark"><span class="wordmark">Norvex</span></div>
    <svg class="feature-arrow" width="8" height="14"><path d="M1 1l6 6-6 6" fill="none" stroke="#6e4e14" stroke-width="2"/></svg>
    <h3>Latest NORVEX</h3>
    <p>Lorem ipsum dolor sit amet, consectetur adipiscing elit. Integer id dolor magna. Aliquam elit metus, laoreet et mattis eu,</p>
  </article>
  <article class="abs feature" style="left:778px">
    <div class="feature-mark"><svg width="60" height="44" viewBox="0 0 60 44"><g fill="#8a6422"><circle cx="22" cy="18" r="11"/><circle cx="42" cy="32" r="8"/></g><g fill="none" stroke="#8a6422" stroke-width="5" stroke-dasharray="4 4.6"><circle cx="22" cy="18" r="13.5"/><circle cx="42" cy="32" r="10"/></g><circle cx="22" cy="18" r="4.5" fill="#efefef"/><circle cx="42" cy="32" r="3.5" fill="#efefef"/></svg></div>
    <svg class="feature-arrow" width="8" height="14"><path d="M1 1l6 6-6 6" fill="none" stroke="#6e4e14" stroke-width="2"/></svg>
    <h3>Services Beyond</h3>
    <p>Lorem ipsum dolor sit amet, consectetur adipiscing elit. Integer id dolor magna. Aliquam elit metus, laoreet et mattis eu,</p>
  </article>

  <div class="abs partners">
    <span class="partners-label">Partners :</span>
    <span class="partner-badge partner-wide" style="margin-left:6px"></span><span class="partner-badge partner-round"></span>
    <span class="partner-badge partner-wide"></span><span class="partner-badge partner-round"></span>
    <span class="partner-badge partner-wide"></span><span class="partner-badge partner-round"></span>
  </div>
</section>

<section class="abs panel about">
  <div class="panel-head">About Us</div>
  <div class="about-photo" role="img" aria-label="Portrait photo of the company director"></div>
  <h2 class="about-hello">Hello there !</h2>
  <p class="about-text">Lorem ipsum dolor sit amet, consectetur adipiscing elit. Integer id dolor magna. Aliquam elit metus, laoreet et mattis eu, bibendum ac risus. Pellentesque odio nisi, iaculis eget ornare et, pulvinar eget nibh. Nunc a arcu augue. Cras hendrerit tincidunt ligula a porta. Maecenas scelerisque tortor arcu, ac porta lorem auctor id. Quisque aliquam ipsum ut enim malesuada, nec fringilla nulla dictum.</p>
  <span class="readmore">readmore</span>
</section>

<section class="abs panel news">
  <div class="panel-head">Latest News</div>
  <div class="news-dots"><i></i><i class="on"></i><i></i><i></i><i></i></div>
  <div class="news-date"><span class="news-day">3</span>JULY<br>2013</div>
  <div class="news-photo" role="img" aria-label="Photo of business people meeting at a laptop"></div>
  <h3 class="news-title">HEADER TITLE HERE</h3>
  <p class="news-text">Lorem ipsum dolor sit amet, consectetur adipiscing elit. Integer id dolor magna. Aliquam elit metus, laoreet et mattis eu, bibendum ac risus. Pellentesque odio nisi, iaculis eget ornare et, pulvinar eget nibh. Nunc a arcu</p>
</section>

<div class="abs footer-band"></div>
<footer class="abs site-footer">
  <div class="abs newsletter"><div>Enter e-mail for newsletter</div></div>
  <svg class="abs newsletter-go" width="13" height="13" viewBox="0 0 13 13"><circle cx="6.5" cy="6.5" r="6" fill="#555"/><path d="M5 3.5l3 3-3 3" fill="none" stroke="#fff" stroke-width="1.5"/></svg>
  <div class="abs socials"><span></span><span></span><span></span><span></span></div>
  <address class="abs company">
    <strong>Tadurk Information System</strong>
    Rue des Tilleuls 12 - 4100<br>Marbelle - Belgium<br>Phone: +32 (0)61 40 52 19<br>Fax: +32 (0)61 40 52 20
  </address>

  <nav class="abs foot-col" style="left:445px"><h4>SOLUTIONS</h4>Korvin ERP Norvex<br>Financial Management<br>Korvin ERP Norvex<br>Financial Management<br>Korvin ERP Norvex<br>Financial Management</nav>
  <nav class="abs foot-col" style="left:552px"><h4>HARDWARE</h4>Submenu item 1<br>Submenu item 2<br>Submenu item 3<br>Submenu item 4<br>Submenu item 5<br>Submenu item 6</nav>
  <nav class="abs foot-col" style="left:631px"><h4>SERVICES</h4>Submenu item 1<br>Submenu item 2<br>Submenu item 3<br>Submenu item 4<br>Submenu item 5<br>Submenu item 6</nav>
  <nav class="abs foot-col" style="left:709px"><h4>CLIENTS</h4>Submenu item 1<br>Submenu item 2<br>Submenu item 3<br>Submenu item 4<br>Submenu item 5<br>Submenu item 6</nav>
  <nav class="abs foot-col" style="left:790px"><h4>ABOUT US</h4>Submenu item 1<br>Submenu item 2<br>Submenu item 3<br>Submenu item 4<br>Submenu item 5<br>Submenu item 6</nav>
  <nav class="abs foot-col" style="left:876px"><h4>CONTACT US</h4>Inquiry<br>Location</nav>

  <div class="abs foot-rule"></div>
  <p class="abs copyright">Copyright Ondesk Solutions. All rights reserved.</p>
  <p class="abs legal">Terms &amp; Conditions | Privacy | Sitemap</p>
</footer>

</body>
</html>
```